Business Card Design

Buy and sell properties
Buy and rehab properties
Buy properties for cash
That is what I do but do need a logo
looking for some type of logo or design on it
Just started business
Back of card should say something like BUY HOUSES CASH
Overview: it is a new company. Basically I buy properties wholesale and fix them up and sell them or sell them to other fix and flippers
Background: company is new so not any background
Market: is basically anyone selling a house or buying a house. Someone that needs to sell house fast. Basically I am a cash home buyer!!!

Updates
Email on card should be:   harborlanerealtyinc@mailnest.com

Industry/Entity Type
House
Contact Information for Business Card
Harbor Lane Realty Inc
PO Box 718296
Coral Mill Key FL 33071

Dwight Kallum
dkallum@mailnest.com
305-271-5589

```html
<!DOCTYPE html>
<html lang="en">
<head>
<meta charset="utf-8">
<title>Harbor Lane Realty Inc – Business Card</title>
<link href="https://fonts.googleapis.com/css2?family=Cormorant+SC:wght@500&family=Tinos&display=swap" rel="stylesheet">
<style>
  :root {
    --lime: #a6ce39;
    --ink: #1c1a1b;
    --paper: #ffffff;
    --backdrop: #d9d6d2;
  }
  html, body {
    margin: 0;
    width: 1200px;
    height: 1023px;
    overflow: hidden;
    background: var(--backdrop);
  }
  .sheet {
    position: relative;
    width: 1200px;
    height: 1023px;
  }
  .card {
    position: absolute;
    left: 200px;
    width: 800px;
    height: 457px;
    box-shadow: 0 6px 18px rgba(0,0,0,.18);
    overflow: hidden;
    background: var(--lime);
  }
  .card--front { top: 40px; }
  .card--back  { top: 526px; }

  .front-panel {
    position: absolute;
    left: 0;
    top: 0;
    bottom: 0;
    width: 340px;
    background: var(--paper);
    border-right: 6px solid var(--ink);
  }

  .brand {
    position: absolute;
    left: 40px;
    top: 190px;
    display: flex;
    align-items: center;
    gap: 14px;
    font-family: "Cormorant SC", serif;
    font-weight: 500;
    color: var(--ink);
  }
  .brand__dot {
    width: 44px; height: 44px;
    border-radius: 50%;
    background: var(--lime);
    flex: none;
  }
  .brand__name { font-size: 30px; line-height: 1.05; letter-spacing: 1px; }

  .holder {
    position: absolute;
    right: 40px;
    top: 70px;
    font-family: "Tinos", serif;
    font-size: 34px;
    color: var(--ink);
  }
  .contact {
    position: absolute;
    right: 40px;
    top: 250px;
    margin: 0;
    padding: 0;
    list-style: none;
    font-family: "Tinos", serif;
    font-size: 20px;
    color: var(--ink);
    text-align: right;
  }
  .contact li {
    display: flex;
    justify-content: flex-end;
    align-items: center;
    gap: 12px;
    line-height: 34px;
  }
  .contact svg { width: 16px; height: 16px; fill: var(--ink); flex: none; }

  .back-text {
    position: absolute;
    inset: 0;
    display: flex;
    flex-direction: column;
    align-items: center;
    justify-content: center;
    color: var(--ink);
  }
  .back-text__company {
    font-family: "Cormorant SC", serif;
    font-weight: 500;
    font-size: 46px;
    line-height: 1;
    text-align: center;
    letter-spacing: 1px;
  }
  .back-text__tagline {
    margin-top: 34px;
    font-family: "Cormorant SC", serif;
    font-weight: 500;
    font-size: 34px;
    letter-spacing: 1px;
  }
</style>
</head>
<body>
<main class="sheet">
  <section class="card card--front">
    <div class="front-panel"></div>

    <div class="brand">
      <span class="brand__dot"></span>
      <span class="brand__name">Harbor Lane<br>Realty Inc</span>
    </div>

    <div class="holder">Dwight Kallum</div>

    <ul class="contact">
      <li>305-271-5589
        <svg viewBox="0 0 16 16"><path d="M3 1h3l1.5 4-2 1.3a9 9 0 0 0 4.2 4.2L11 8.5l4 1.5v3c0 1-1 2-2 2A12 12 0 0 1 1 3c0-1 1-2 2-2z"/></svg>
      </li>
      <li>dkallum@mailnest.com
        <svg viewBox="0 0 16 16"><path d="M1 3h14v10H1z M2 4.5v.3l6 4 6-4v-.3z" fill-rule="evenodd"/></svg>
      </li>
      <li>718296 Coral Mill Key FL 33071
        <svg viewBox="0 0 16 16"><path d="M8 0a5 5 0 0 0-5 5c0 4 5 11 5 11s5-7 5-11a5 5 0 0 0-5-5zm0 7a2 2 0 1 1 0-4 2 2 0 0 1 0 4z"/></svg>
      </li>
    </ul>
  </section>

  <section class="card card--back">
    <div class="back-text">
      <div class="back-text__company">Harbor Lane<br>Realty Inc</div>
      <div class="back-text__tagline">Buy Houses Cash</div>
    </div>
  </section>
</main>
</body>
</html>
```